Healthy lifestyle Influencer business card

I need your creativity to have a business card that I can leave in all the restaurants, hotels and spas I visit to inform them that I am an influencer specializing in the wellness sector and that I will write a review about them. You can use my instagram photos Lunavita27 or on my website www.piattileggeriorto.it. I would like my business card to impress with its creativity! thank you very much!

Contact Information for Business Card

siteweb, instagram, phone number

Font styles to use
Decorative
Script

Colors
0094D4
00A9DD
6FCCEA
C7EBF8
E9F6FB
59FF00
82FF00
B8FF75
E3FFCB
F4FFEA
FFC000
F8CF3A
FAE287
FDF2CF
FEFAEE
F0912C
F2A743
F7CA91
FBE8D2
FDF5EE
EE7325
F08F49
F5BC92
FAE3D3
FDF4ED
EB3D1F
EC4F4E
F09395
F8D3D4
FCEDEE
E54698
E96AAD
F1A4CE
F9D9EA
FCEFF6

Requirements
Nice to have
• creativity

```html
<!DOCTYPE html>
<html lang="it">
<head>
<meta charset="utf-8">
<title>Luna Vita Chef – Biglietto da visita</title>
<link rel="stylesheet" href="https://fonts.googleapis.com/css2?family=Great+Vibes&family=Jost:wght@400&family=Roboto:wght@300;400&display=swap">
<style>
  :root {
    --bg: #2a2a2b;
    --sage: #93b8b0;
    --paper: #efefef;
    --ink: #3f3f41;
    --ink-soft: #555557;
    --accent: #8fb7ae;
  }
  * { box-sizing: border-box; margin: 0; padding: 0; }
  html, body { width: 1138px; height: 1200px; overflow: hidden; }
  body { background: var(--bg); position: relative; font-family: "Roboto", sans-serif; }

  .card {
    position: absolute;
    top: 272px;
    width: 375px;
    height: 622px;
    border-radius: 16px;
    overflow: hidden;
  }
  .card--back { left: 158px; background: var(--sage); }
  .card--front { left: 578px; background: var(--paper); text-align: center; color: var(--ink); }

  .brand-name {
    font-family: "Jost", sans-serif;
    font-weight: 400;
    color: var(--ink);
    line-height: 1;
    letter-spacing: 1px;
    white-space: nowrap;
  }
  .tagline {
    font-family: "Jost", sans-serif;
    font-weight: 400;
    color: var(--ink);
    font-size: 16px;
    white-space: nowrap;
  }

  /* back side: rotated lockup */
  .back-lockup {
    position: absolute;
    left: 188px;
    top: 288px;
    width: 440px;
    transform: translate(-50%, -50%) rotate(-90deg);
    text-align: center;
  }
  .back-lockup .brand-name { font-size: 44px; }
  .back-lockup .tagline { font-size: 18px; margin-top: 10px; }

  .social {
    position: absolute;
    left: 0; right: 0;
    bottom: 36px;
    display: flex;
    justify-content: center;
    align-items: center;
    gap: 10px;
    font-family: "Roboto", sans-serif;
    font-size: 16px;
    color: var(--ink);
  }
  .social__dot {
    width: 14px; height: 14px;
    border-radius: 50%;
    background: var(--ink);
  }

  /* front side */
  .front-lockup { position: absolute; top: 136px; left: 0; right: 0; }
  .front-lockup .brand-name { font-size: 40px; }
  .front-lockup .tagline { margin-top: 12px; }

  .person-name {
    position: absolute;
    top: 318px; left: 0; right: 0;
    font-family: "Great Vibes", cursive;
    font-size: 34px;
    color: var(--ink);
  }

  .divider {
    position: absolute;
    top: 388px; left: 74px; right: 74px;
    display: flex;
    align-items: center;
    gap: 10px;
  }
  .divider__line { flex: 1; height: 2px; background: var(--ink); }
  .divider__icons { display: flex; gap: 3px; }
  .divider__icons svg { width: 25px; height: 25px; display: block; }

  .contact {
    position: absolute;
    top: 434px; left: 0; right: 0;
    font-family: "Roboto", sans-serif;
    font-weight: 300;
    font-size: 16px;
    line-height: 24px;
    color: var(--ink-soft);
  }
</style>
</head>
<body>

<section class="card card--back">
  <div class="back-lockup">
    <div class="brand-name">Luna Vita Chef</div>
    <div class="tagline">Benessere in ogni piatto</div>
  </div>
  <div class="social">
    <span class="social__dot"></span>
    <span class="social__handle">@Lunavita27</span>
  </div>
</section>

<section class="card card--front">
  <div class="front-lockup">
    <div class="brand-name">Luna Vita Chef</div>
    <div class="tagline">Benessere in ogni piatto</div>
  </div>

  <div class="person-name">Luna Ferraro</div>

  <div class="divider">
    <span class="divider__line"></span>
    <span class="divider__icons">
      <svg viewBox="0 0 24 24" aria-label="telefono" role="img">
        <circle cx="12" cy="12" r="10.5" fill="none" stroke="var(--accent)" stroke-width="1.5"/>
        <path d="M7 10c0-1.5 2-2.5 5-2.5s5 1 5 2.5l-1.6.6-.6-1.4h-5.6l-.6 1.4z M8.5 12h7l1 4h-9z" fill="var(--accent)"/>
      </svg>
      <svg viewBox="0 0 24 24" aria-label="email" role="img">
        <circle cx="12" cy="12" r="10.5" fill="none" stroke="var(--accent)" stroke-width="1.5"/>
        <rect x="6.5" y="8.5" width="11" height="7.5" fill="none" stroke="var(--accent)" stroke-width="1.4"/>
        <path d="M6.5 8.5l5.5 4.2 5.5-4.2" fill="none" stroke="var(--accent)" stroke-width="1.4"/>
      </svg>
      <svg viewBox="0 0 24 24" aria-label="sito web" role="img">
        <circle cx="12" cy="12" r="10.5" fill="none" stroke="var(--accent)" stroke-width="1.5"/>
        <circle cx="12" cy="12" r="6" fill="none" stroke="var(--accent)" stroke-width="1.2"/>
        <ellipse cx="12" cy="12" rx="2.6" ry="6" fill="none" stroke="var(--accent)" stroke-width="1.1"/>
        <path d="M6 12h12M7 9h10M7 15h10" stroke="var(--accent)" stroke-width="1"/>
      </svg>
    </span>
    <span class="divider__line"></span>
  </div>

  <div class="contact">
    <div class="contact__phone">000-0000-0000</div>
    <div class="contact__email">info@piattileggeriorto.it</div>
    <div class="contact__web">www.piattileggeriorto.it</div>
  </div>

  <div class="social">
    <span class="social__dot"></span>
    <span class="social__handle">@Lunavita27</span>
  </div>
</section>

</body>
</html>
```